New business card/stationary for a consulting company

I am looking for a clean and very professional looking business card for my consulting company as well as corresponding stationary. I am uploading our logo. I like simple and powerful for the feel. No graphics but I am open on everything else. Below is my contact information but would like the final to be in a version I can add my employees information into and print. Thank you.

Daniel Whitcombe
dan@ferncliffadvisory.com
2870 North 9th Avenue, Summit Floor, Elm Ridge, Illinois 60531
www.ferncliffadvisory.com

Industry/Entity Type

Consulting

Contact Information for Business Card

Daniel Whitcombe
dan@ferncliffadvisory.com
www.ferncliffadvisory.com

Font styles to use
Serif
Sans Serif

Requirements
Must have
• Our logo and the business card details.
Nice to have
• our website www.ferncliffadvisory.com

```html
<!DOCTYPE html>
<html lang="en">
<head>
<meta charset="utf-8">
<title>Ferncliff Advisory – Business Card</title>
<link rel="stylesheet" href="https://fonts.googleapis.com/css2?family=Montserrat:wght@300;400;500;600;700&display=swap">
<style>
  :root {
    --navy: #1f1d85;
    --white: #ffffff;
    --backdrop: #ececec;
    --card-shadow: rgba(0, 0, 0, 0.14);
  }
  * { box-sizing: border-box; margin: 0; padding: 0; }
  html, body {
    width: 1200px;
    height: 1000px;
    overflow: hidden;
    background: var(--backdrop);
    font-family: "Montserrat", sans-serif;
  }
  .business-card {
    position: absolute;
    left: 100px;
    top: 215px;
    width: 1000px;
    height: 570px;
    background: var(--white);
    box-shadow: 0 10px 30px var(--card-shadow);
    overflow: hidden;
  }
  .brand-band {
    position: absolute;
    left: 0;
    top: 0;
    width: 1000px;
    height: 570px;
  }
  .brand-lockup {
    position: absolute;
    top: 120px;
    left: 0;
    width: 100%;
    display: flex;
    align-items: center;
    justify-content: center;
    gap: 18px;
  }
  .brand-square {
    width: 34px;
    height: 34px;
    background: var(--navy);
  }
  .brand-name {
    color: var(--navy);
    font-weight: 400;
    font-size: 40px;
    letter-spacing: 3px;
  }
  .person {
    position: absolute;
    right: 530px;
    top: 305px;
    text-align: right;
    color: var(--white);
  }
  .person-name {
    font-weight: 700;
    font-size: 34px;
    letter-spacing: 0.3px;
  }
  .person-title {
    font-weight: 300;
    font-size: 20px;
    margin-top: 4px;
  }
  .divider {
    position: absolute;
    left: 500px;
    top: 300px;
    width: 2px;
    height: 82px;
    background: var(--white);
  }
  .contact-list {
    position: absolute;
    left: 528px;
    top: 308px;
    list-style: none;
    color: var(--white);
    font-size: 22px;
  }
  .contact-item {
    display: flex;
    align-items: center;
    gap: 14px;
    height: 34px;
  }
  .contact-item strong { font-weight: 600; }
  .contact-item span { font-weight: 400; }
  .contact-icon { width: 18px; height: 18px; flex: none; }
  .address {
    position: absolute;
    left: 0;
    top: 455px;
    width: 100%;
    text-align: center;
    color: var(--white);
    font-weight: 600;
    font-size: 24px;
    letter-spacing: 0.3px;
  }
</style>
</head>
<body>
  <main class="business-card">
    <svg class="brand-band" viewBox="0 0 1000 570" aria-hidden="true">
      <path d="M0 250 H478 L494 268 L510 250 H1000 V570 H0 Z" fill="var(--navy)"/>
    </svg>

    <div class="brand-lockup">
      <div class="brand-square"></div>
      <div class="brand-name">FERNCLIFF ADVISORY</div>
    </div>

    <div class="person">
      <div class="person-name">Daniel Whitcombe</div>
      <div class="person-title">Founder / Principal</div>
    </div>

    <div class="divider"></div>

    <ul class="contact-list">
      <li class="contact-item">
        <svg class="contact-icon" viewBox="0 0 18 18" aria-hidden="true">
          <rect x="1" y="4" width="16" height="11" fill="var(--white)"/>
          <path d="M1 4 L9 10 L17 4" fill="none" stroke="var(--navy)" stroke-width="1.5"/>
        </svg>
        <div><span>dan@</span><strong>ferncliffadvisory</strong><span>.com</span></div>
      </li>
      <li class="contact-item">
        <svg class="contact-icon" viewBox="0 0 18 18" aria-hidden="true">
          <circle cx="9" cy="9" r="8" fill="var(--white)"/>
          <g fill="none" stroke="var(--navy)" stroke-width="1.2">
            <ellipse cx="9" cy="9" rx="3.5" ry="8"/>
            <line x1="1" y1="9" x2="17" y2="9"/>
            <line x1="2.5" y1="5" x2="15.5" y2="5"/>
            <line x1="2.5" y1="13" x2="15.5" y2="13"/>
          </g>
        </svg>
        <div><span>www.</span><strong>ferncliffadvisory</strong><span>.com</span></div>
      </li>
    </ul>

    <p class="address">2870 North 9th Avenue, Summit Floor, Elm Ridge, Illinois 60531</p>
  </main>
</body>
</html>
```